Satchel & Sundial needs new business card design

I need a new business card design. I'm looking for out-of-the-box design which represents the freedom of being a location independent entrepreneur.
I offer coaching, retreats and trips.
I would like to see designs with and without the photo.
Colors I use are black (#000000), green (#25A796) and brown (#D7C38C)
Website satchelandsundial.example

Target Market(s)

location independent entrepreneurs, digital nomads, people looking to swap the 9 to 5 for a lifestyle business

Industry/Entity Type

Business

Contact Information for Business Card

Dorota Falkner
Your Lifestyle Business Coach, Retreat & Trip Leader
http://satchelandsundial.example
hello@satchelandsundial.example
Live a life you don't need a holiday from

Font styles to use
Serif
Sans Serif

Requirements
Must have
• One side should contain only the logo. I would also consider having the "Live a life you don't need a holiday from" on that side too (depending on how it looks)
• Please show both sides on the designs.

```html
<!DOCTYPE html>
<html lang="en">
<head>
<meta charset="utf-8">
<title>Satchel &amp; Sundial – Business Card</title>
<link rel="stylesheet" href="https://fonts.googleapis.com/css2?family=Arimo:wght@400;700&display=swap">
<style>
  :root {
    --stage: #3b3c3e;
    --teal: #25a796;
    --teal-deep: #1c8f80;
    --teal-pale: #a9dcd5;
    --ink: #1f1f1f;
    --ink-soft: #444444;
    --grey: #7a7a7a;
    --paper: #ffffff;
    --paper-shade: #ececec;
    --band-dark: #2a2a2a;
  }
  * { box-sizing: border-box; margin: 0; padding: 0; }
  html, body { width: 1200px; height: 843px; overflow: hidden; }
  body {
    background: var(--stage);
    font-family: "Arimo", Arial, sans-serif;
    position: relative;
  }
  .card {
    position: absolute;
    width: 540px;
    height: 309px;
    border-radius: 3px;
    overflow: hidden;
    box-shadow: 0 10px 28px rgba(0,0,0,.45);
  }

  /* Logo side */
  .card--back {
    left: 80px; top: 110px;
    background: linear-gradient(135deg, var(--teal) 0%, var(--teal-deep) 100%);
    color: var(--paper);
  }
  .card--back .brand-name {
    position: absolute;
    left: 0; right: 0; top: 100px;
    text-align: center;
    font-size: 44px;
    font-weight: 700;
    letter-spacing: 1px;
    text-transform: uppercase;
  }
  .card--back .rule {
    position: absolute;
    left: 90px; right: 90px; top: 228px;
    height: 1px;
    background: rgba(255,255,255,.55);
  }
  .card--back .motto {
    position: absolute;
    left: 0; right: 0; top: 244px;
    text-align: center;
    font-size: 15px;
    letter-spacing: .5px;
    color: rgba(255,255,255,.9);
  }

  /* Contact side */
  .card--front {
    left: 580px; top: 420px;
    background: linear-gradient(160deg, var(--paper) 55%, var(--paper-shade) 100%);
    color: var(--ink);
  }
  .card--front .brand-name {
    position: absolute;
    left: 40px; top: 36px;
    font-size: 38px;
    font-weight: 700;
    letter-spacing: 1px;
    text-transform: uppercase;
    color: var(--ink);
  }
  .contact {
    position: absolute;
    left: 40px; top: 120px;
    line-height: 1.35;
  }
  .contact .person { color: var(--teal); font-size: 19px; margin-bottom: 2px; }
  .contact .role { font-size: 15px; color: var(--ink-soft); }
  .contact .email { margin-top: 10px; font-size: 14px; color: var(--grey); }
  .contact .email b { color: var(--teal); font-weight: 700; margin-right: 6px; }
  .bands { position: absolute; left: 0; bottom: 0; width: 540px; height: 70px; }
  .website {
    position: absolute;
    right: 22px; bottom: 19px;
    color: var(--paper);
    font-size: 14px;
    font-weight: 700;
    letter-spacing: 1.5px;
    white-space: nowrap;
  }
</style>
</head>
<body>

<section class="card card--back" aria-label="Logo side">
  <div class="brand-name">Satchel &amp; Sundial</div>
  <div class="rule"></div>
  <p class="motto">Live a life you don't need a holiday from</p>
</section>

<section class="card card--front" aria-label="Contact side">
  <div class="brand-name">Satchel &amp; Sundial</div>
  <div class="contact">
    <p class="person">Dorota Falkner</p>
    <p class="role">Your Lifestyle Business Coach<br>Retreat &amp; Trip Leader</p>
    <p class="email"><b>E :</b>hello@satchelandsundial.example</p>
  </div>
  <svg class="bands" viewBox="0 0 540 70" aria-hidden="true">
    <polygon points="0,4 238,4 226,18 0,18" fill="#25a796"/>
    <polygon points="0,18 226,18 222,23 0,23" fill="#a9dcd5"/>
    <polygon points="228,16 540,16 540,70 190,70" fill="#2a2a2a"/>
  </svg>
  <div class="website">www.satchelandsundial.example</div>
</section>

</body>
</html>
```